New Bicycle shop business card

Hi!
I'm looking for a business card for my new proffesional bike mechanics shop. This shop is only for fixing broken bikes and not selling bikes.
Peferbly a modern and sleek and modern design.
Colors: black, grey, red, white
Information:
Name: Rijwielwerkplaats Vanhoutte
Shop owner: Bart Vanhoutte & Marieke Segers
Website: www.rijwielwerkplaats-vanhoutte.be
Email: info@rijwielwerkplaats-vanhoutte.be
Phone number: +32471902368
Street adres: Kerkweg 46
9940 Bellebeke
Slogan/shop information: Herstellingen van alle merken.
Logo: see files.
Target Market(s)
People who seek a mechanic to fix or upgrade their bikes.
Contact Information for Business Card
Information:
Website: info@rijwielwerkplaats-vanhoutte.be
9940 Bellebeke
Logo: see files.

```html
<!DOCTYPE html>
<html lang="nl">
<head>
<meta charset="utf-8">
<title>Rijwielwerkplaats Vanhoutte – Business Card</title>
<link rel="stylesheet" href="https://fonts.googleapis.com/css2?family=Josefin+Sans:wght@700&family=Roboto:wght@400&display=swap">
<style>
  :root {
    --page-bg: #e4e2df;
    --card-bg: #f4f3f1;
    --card-edge: #d6d3cf;
    --ink: #1f1f1f;
    --ink-soft: #2b2b2b;
    --brand-red: #c8303e;
  }
  * { margin: 0; padding: 0; box-sizing: border-box; }
  html, body {
    width: 1200px;
    height: 1054px;
    overflow: hidden;
    background: var(--page-bg);
  }
  .card {
    position: absolute;
    left: 100px;
    top: 227px;
    width: 1000px;
    height: 600px;
    background: var(--card-bg);
    border: 1px solid var(--card-edge);
    border-radius: 6px;
    overflow: hidden;
  }
  .company-name {
    position: absolute;
    left: 46px;
    top: 78px;
    font-family: "Josefin Sans", sans-serif;
    font-weight: 700;
    font-size: 38px;
    line-height: 1.05;
    letter-spacing: 2px;
    color: var(--ink);
    text-transform: uppercase;
  }
  .company-name .line { display: block; }
  .company-name .line-second { letter-spacing: 9px; }
  .person-name {
    position: absolute;
    left: 46px;
    top: 262px;
    font-family: "Josefin Sans", sans-serif;
    font-weight: 700;
    font-size: 34px;
    letter-spacing: 1px;
    color: var(--brand-red);
    text-transform: uppercase;
  }
  .person-role {
    position: absolute;
    left: 46px;
    top: 306px;
    font-family: "Roboto", sans-serif;
    font-size: 22px;
    color: var(--ink-soft);
  }
  .contact-list {
    position: absolute;
    left: 46px;
    top: 410px;
    list-style: none;
    font-family: "Roboto", sans-serif;
    font-size: 22px;
    color: var(--ink);
  }
  .contact-item {
    display: flex;
    align-items: center;
    height: 38px;
  }
  .contact-icon {
    width: 22px;
    height: 22px;
    margin-right: 28px;
    fill: var(--brand-red);
    flex: none;
  }
  .address {
    position: absolute;
    left: 46px;
    top: 530px;
    font-family: "Roboto", sans-serif;
    font-size: 22px;
    color: var(--ink);
  }
  .brand-block {
    position: absolute;
    right: 60px;
    top: 110px;
    width: 340px;
    height: 340px;
    background: var(--brand-red);
  }
</style>
</head>
<body>
  <div class="card">
    <h1 class="company-name">
      <span class="line">Rijwielwerkplaats</span>
      <span class="line line-second">Vanhoutte</span>
    </h1>

    <p class="person-name">Marieke Segers</p>
    <p class="person-role">Owner</p>

    <ul class="contact-list">
      <li class="contact-item">
        <svg class="contact-icon" viewBox="0 0 24 24" aria-hidden="true">
          <path d="M6.6 10.8a15.1 15.1 0 0 0 6.6 6.6l2.2-2.2a1 1 0 0 1 1-.25 11.4 11.4 0 0 0 3.6.57 1 1 0 0 1 1 1V20a1 1 0 0 1-1 1A17 17 0 0 1 3 4a1 1 0 0 1 1-1h3.5a1 1 0 0 1 1 1c0 1.25.2 2.45.57 3.57a1 1 0 0 1-.25 1z"/>
        </svg>
        <span>+32471902368</span>
      </li>
      <li class="contact-item">
        <svg class="contact-icon" viewBox="0 0 24 24" aria-hidden="true">
          <path d="M2 5h20v14H2z M4 7v.4l8 5.2 8-5.2V7l-8 5.2z" fill-rule="evenodd"/>
        </svg>
        <span>www.rijwielwerkplaats-vanhoutte.be</span>
      </li>
      <li class="contact-item">
        <svg class="contact-icon" viewBox="0 0 24 24" aria-hidden="true">
          <path d="M12 2a10 10 0 1 0 0 20 10 10 0 0 0 0-20zm6.9 6h-2.9a15.7 15.7 0 0 0-1.4-3.6A8 8 0 0 1 18.9 8zM12 4a14 14 0 0 1 1.9 4h-3.8A14 14 0 0 1 12 4zM4.3 14a8 8 0 0 1 0-4h3.4a16 16 0 0 0 0 4zm.8 2h2.9a15.7 15.7 0 0 0 1.4 3.6A8 8 0 0 1 5.1 16zM8 8H5.1a8 8 0 0 1 4.3-3.6A15.7 15.7 0 0 0 8 8zm4 12a14 14 0 0 1-1.9-4h3.8A14 14 0 0 1 12 20zm2.3-6H9.7a14.6 14.6 0 0 1 0-4h4.6a14.6 14.6 0 0 1 0 4zm.3 5.6A15.7 15.7 0 0 0 16 16h2.9a8 8 0 0 1-4.3 3.6zM16.3 14a16 16 0 0 0 0-4h3.4a8 8 0 0 1 0 4z"/>
        </svg>
        <span>info@rijwielwerkplaats-vanhoutte.be</span>
      </li>
    </ul>

    <p class="address">Kerkweg 46 9940 Bellebeke</p>

    <div class="brand-block" aria-hidden="true"></div>
  </div>
</body>
</html>
```